DRUM needs a contemporary simple brochure

We help companies understand their customers, and we would like to send a minimalistic card/brochure to potential clients to introduce our company. The card will be A6 in size (ie A5 folded once) and so will have a front, an inside front, and inside back, and a back page. It can either be portrait or landscape.
It should convey contemporary/modern, bold, fun, uncomplicated/simplicity, be clean/uncluttered, and use friendly and easy to read fonts.
Attached is the information the brochure/card should contain, together with colour palatte and another document which shows our logo, existing stationary etc to give you a feel of the brand. The background of the card could be black, yellow or white (or a combination). thanks, mark
Updates
Hi everyone. Just to let you know that the card will be A6 size, will have a matt laminate finish and can include spot uv. thanks, mark
Reason: Hi, I am looking for some better quality designs so i have extended the deadline and significantly increased the budget. thanks, mark
Target Market(s)
Marketing professionals in large corporates
Industry/Entity Type
It Company
Requirements
Must have
- use our company colours (attached)

```html
<!DOCTYPE html>
<html lang="en">
<head>
<meta charset="utf-8">
<title>DRUM – Brochure Spread</title>
<link rel="stylesheet" href="https://fonts.googleapis.com/css2?family=PT+Sans:wght@400;700&display=swap">
<style>
  :root {
    --charcoal: #3d3d3f;
    --paper: #ffffff;
    --yellow: #fdd84a;
    --yellow-pale: #fff2c4;
    --brand-yellow: #f5c400;
    --stage: #e8e3da;
    --text-soft: #4a4a4a;
    --bar-text: #d9d9d9;
  }
  * { box-sizing: border-box; margin: 0; padding: 0; }
  html, body {
    width: 1200px; height: 960px; overflow: hidden;
    background: var(--stage);
    font-family: "PT Sans", Arial, sans-serif;
  }
  .spread {
    position: absolute; left: 50px; top: 92px;
    width: 1100px; height: 776px;
    background: var(--paper);
    box-shadow: 0 6px 18px rgba(0,0,0,.25);
    overflow: hidden;
  }
  .top-bar, .bottom-bar {
    position: absolute; left: 0; width: 100%;
    background: var(--charcoal);
  }
  .top-bar { top: 0; height: 59px; }
  .bottom-bar { bottom: 0; height: 46px; }
  .yellow-band {
    position: absolute; left: 0; top: 273px; width: 100%; height: 194px;
    background: linear-gradient(to bottom, var(--yellow), var(--yellow-pale));
  }
  .notch { position: absolute; left: 0; top: 0; }
  .back-name, .front-name {
    position: absolute; font-weight: 700; letter-spacing: -1px;
    line-height: 1; white-space: nowrap;
  }
  .back-name {
    left: 273px; top: 369px; transform: translate(-50%, -50%);
    font-size: 50px; color: var(--charcoal);
  }
  .front-name {
    left: 822px; top: 146px; transform: translate(-50%, -50%);
    font-size: 86px; color: var(--brand-yellow);
  }
  .cover-photo {
    position: absolute; left: 622px; top: 218px; width: 403px; height: 295px;
    background:
      linear-gradient(to bottom, rgba(255,255,255,0) 75%, rgba(255,255,255,.9)),
      linear-gradient(100deg, #7d8f5a 0%, #c9cbb8 30%, #e9e6de 55%, #5a544c 80%, #2d2d2f 100%);
  }
  .tagline {
    position: absolute; left: 822px; top: 541px; transform: translate(-50%, -50%);
    font-size: 15px; letter-spacing: 1px; color: var(--text-soft); white-space: nowrap;
  }
  .contact {
    position: absolute; left: 273px; top: 612px; transform: translateX(-50%);
    text-align: center; color: var(--text-soft); font-size: 9.5px; line-height: 12px;
    white-space: nowrap;
  }
  .contact .name { font-weight: 700; font-size: 11px; margin-bottom: 10px; }
  .contact .gap { height: 12px; }
  .web {
    position: absolute; left: 822px; bottom: 23px; transform: translate(-50%, 50%);
    font-size: 12px; letter-spacing: 7px; color: var(--bar-text); white-space: nowrap;
  }
</style>
</head>
<body>
  <section class="spread">
    <div class="top-bar"></div>
    <div class="yellow-band"></div>
    <svg class="notch" width="1100" height="280" viewBox="0 0 1100 280" aria-hidden="true">
      <polygon points="474,58 622,58 548,273" fill="var(--charcoal)"/>
    </svg>

    <p class="back-name">drum</p>

    <div class="contact">
      <p class="name">DRUM</p>
      <p>Level 6</p>
      <p>14 Harbour Lane</p>
      <p>Redfern Park, NSW, 2016</p>
      <div class="gap"></div>
      <p>02 5550 1234</p>
      <p>info@drumresearch.com.au</p>
    </div>

    <p class="front-name">drum</p>
    <div class="cover-photo" role="img" aria-label="Photo of a bright modern lounge with a white sofa, glass coffee table, patterned rug and potted plants by the window"></div>
    <p class="tagline">Customer &amp; Shopper Market Research</p>

    <div class="bottom-bar"></div>
    <p class="web">www.drumresearch.com.au</p>
  </section>
</body>
</html>
```